Maple Roster Business Card for recruitment company

We are looking for a Business Card Design that incorporates our personal details and our busines name and logo. We are a specialized search consultancy that recruit Property and Construction professionals.
We would like a business card that stands out and is appealing to the Construction and Property industry as well.

Target Market(s)

people in the construction and property industry

Contact Information for Business Card

Business Name and logo

Font styles to use
Serif

Colors
0094D4
00A9DD
6FCCEA
C7EBF8
E9F6FB

Requirements
Must have
• Business name and logo as well as contact details
Should not have
• No photos of us please

```html
<!DOCTYPE html>
<html lang="en">
<head>
<meta charset="utf-8">
<title>Maple Roster Business Card</title>
<link rel="stylesheet" href="https://fonts.googleapis.com/css2?family=Josefin+Sans:wght@300;400;600;700&display=swap">
<style>
  :root {
    --backdrop: #a3a3a3;
    --ink-teal: #023d51;
    --mark-tint: #134e62;
    --paper: #ffffff;
    --text-grey: #6a6a6a;
    --rule-grey: #9a9a9a;
  }
  * { margin: 0; padding: 0; box-sizing: border-box; }
  html, body {
    width: 1200px; height: 1200px; overflow: hidden;
    background: var(--backdrop);
    font-family: "Josefin Sans", sans-serif;
  }
  .stage { position: relative; width: 1200px; height: 1200px; }
  .card {
    position: absolute; top: 303px;
    width: 370px; height: 594px;
  }
  .card--front { left: 200px; background: var(--ink-teal); }
  .card--back { left: 599px; width: 364px; background: var(--paper); }

  .brand-mark-area {
    position: absolute; left: 30px; top: 130px;
    width: 310px; height: 310px;
    background: var(--mark-tint);
  }

  .wordmark {
    position: absolute; left: 0; right: 0;
    text-align: center;
    font-weight: 300;
    font-size: 42px;
    letter-spacing: -1.5px;
    line-height: 1;
    white-space: nowrap;
  }
  .card--front .wordmark { top: 492px; color: var(--paper); }
  .card--back .wordmark { top: 153px; color: var(--ink-teal); }

  .person { position: absolute; left: 0; right: 0; top: 338px; text-align: center; }
  .person__name {
    font-weight: 700; font-size: 28px; line-height: 30px;
    color: var(--ink-teal); letter-spacing: 0.3px;
  }
  .person__role {
    font-weight: 400; font-size: 15px; line-height: 16px;
    color: var(--text-grey); letter-spacing: 0.3px;
  }

  .icon-row {
    position: absolute; left: 87px; width: 190px; top: 396px; height: 25px;
    display: flex; align-items: center; justify-content: center; gap: 4px;
  }
  .icon-row__rule { flex: 1; height: 1px; background: var(--rule-grey); }
  .icon-row__rule:first-child { margin-right: 4px; }
  .icon-row__rule:last-child { margin-left: 4px; }
  .icon-tile {
    width: 25px; height: 25px; border-radius: 3px; background: var(--ink-teal);
    display: flex; align-items: center; justify-content: center;
  }

  .contact {
    position: absolute; left: 0; right: 0; top: 431px;
    text-align: center; font-size: 17px; line-height: 22px; color: var(--text-grey);
  }
  .contact__site-name { color: var(--ink-teal); }
  .divider {
    position: absolute; left: 88px; width: 195px; top: 507px; height: 1px;
    background: var(--rule-grey);
  }
  .address {
    position: absolute; left: 0; right: 0; top: 517px;
    text-align: center; font-size: 17px; line-height: 22px; color: var(--text-grey);
  }
</style>
</head>
<body>
<main class="stage">
  <section class="card card--front" aria-label="Card front">
    <div class="brand-mark-area" role="img" aria-label="Large faint brand symbol belongs here"></div>
    <p class="wordmark">MAPLE ROSTER</p>
  </section>

  <section class="card card--back" aria-label="Card back">
    <p class="wordmark">MAPLE ROSTER</p>

    <div class="person">
      <p class="person__name">DANIEL HARPER</p>
      <p class="person__role">MANAGING DIRECTOR</p>
    </div>

    <div class="icon-row">
      <span class="icon-row__rule"></span>
      <span class="icon-tile">
        <svg width="16" height="14" viewBox="0 0 16 14" aria-label="Phone" role="img">
          <path d="M1 5 Q8 0 15 5 L13 7 L11 5.5 L11 4 Q8 3 5 4 L5 5.5 L3 7 Z" fill="#fff"/>
          <rect x="3.5" y="7" width="9" height="6" rx="1" fill="#fff"/>
          <circle cx="8" cy="10" r="1.6" fill="#023d51"/>
        </svg>
      </span>
      <span class="icon-tile">
        <svg width="16" height="12" viewBox="0 0 16 12" aria-label="Email" role="img">
          <rect x="0.75" y="0.75" width="14.5" height="10.5" fill="none" stroke="#fff" stroke-width="1.3"/>
          <path d="M1 1 L8 7 L15 1 M1 11 L6 5.5 M15 11 L10 5.5" fill="none" stroke="#fff" stroke-width="1.1"/>
        </svg>
      </span>
      <span class="icon-tile">
        <svg width="16" height="16" viewBox="0 0 16 16" aria-label="Website" role="img">
          <circle cx="8" cy="8" r="7" fill="#fff"/>
          <path d="M4 4 Q6 3 7 5 Q6 7 4.5 7 Q3.5 6 4 4 Z M9 8 Q11 7 12 9 Q11 12 9.5 12 Q8.5 10 9 8 Z" fill="#023d51"/>
        </svg>
      </span>
      <span class="icon-row__rule"></span>
    </div>

    <div class="contact">
      <p>044-555 018 274</p>
      <p>info@mapleroster.com</p>
      <p>www.<span class="contact__site-name">mapleroster</span>.com</p>
    </div>

    <div class="divider"></div>

    <div class="address">
      <p>421, Address line here</p>
      <p>45452,Country Name</p>
    </div>
  </section>
</main>
</body>
</html>
```